New LLC consulting company needs a business card design

I need a business card design for new company in Alexandria Virginia called TK Verdane Consulting LLC. The company is focused on consulting for defense and national security issues with expertise in nuclear and space topics. I would like to see designs that are simple and I am open to colors except for brown.

Target Market(s)

All businesses that are seeking consulting help

Industry/Entity Type

Consulting

Contact Information for Business Card

Name of company - TK Verdane Consulting LLC; name (Delia Pratt) President; email: prattdq47@mailvessa.com; Phone: 703-555-0142

Requirements
Must have
• The details described above
Nice to have
• I'm open to all ideas
Should not have
• No brown

```html
<!DOCTYPE html>
<html lang="en">
<head>
<meta charset="utf-8">
<title>TK Verdane Consulting LLC — Business Card</title>
<link href="https://fonts.googleapis.com/css2?family=Roboto:wght@400;500;700&display=swap" rel="stylesheet">
<style>
  :root {
    --stage: #1e1e1e;
    --card-white: #ffffff;
    --brand-blue: #0055a8;
    --ink: #222222;
    --rule: #333333;
  }
  * { margin: 0; padding: 0; box-sizing: border-box; }
  html, body { width: 1200px; height: 1059px; overflow: hidden; background: var(--stage); }
  body { font-family: "Roboto", Arial, sans-serif; }
  .canvas { position: relative; width: 1200px; height: 1059px; }

  .card { position: absolute; border-radius: 24px; overflow: hidden; }
  .card--front { left: 247px; top: 92px; width: 709px; height: 405px; background: var(--card-white); }
  .card--back { left: 247px; top: 557px; width: 700px; height: 400px; background: var(--brand-blue); }

  .wordmark {
    position: absolute; left: 0; right: 0; text-align: center;
    font-weight: 500; text-transform: uppercase; line-height: 1;
  }
  .wordmark__name { display: block; letter-spacing: 2px; }
  .wordmark__legal { display: block; letter-spacing: 6px; margin-top: 12px; }

  .card--front .wordmark { top: 86px; color: var(--brand-blue); }
  .card--front .wordmark__name { font-size: 46px; }
  .card--front .wordmark__legal { font-size: 22px; }

  .card--back .wordmark { top: 146px; color: var(--card-white); }
  .card--back .wordmark__name { font-size: 54px; }
  .card--back .wordmark__legal { font-size: 26px; }

  .holder { position: absolute; left: 38px; top: 258px; }
  .holder__name { font-size: 26px; font-weight: 700; color: var(--brand-blue); line-height: 1.1; }
  .holder__title { font-size: 18px; font-weight: 400; color: var(--ink); margin-top: 4px; }

  .divider { position: absolute; left: 39px; width: 614px; top: 326px; height: 1.5px; background: var(--rule); }

  .contacts {
    position: absolute; left: 37px; right: 52px; top: 343px;
    display: flex; justify-content: space-between; align-items: center;
    font-size: 19px; color: var(--ink);
  }
  .contact { display: flex; align-items: center; gap: 12px; }
  .contact svg { flex: none; }
</style>
</head>
<body>
<div class="canvas">
  <section class="card card--front">
    <div class="wordmark">
      <span class="wordmark__name">TK Verdane</span>
      <span class="wordmark__legal">Consulting LLC</span>
    </div>
    <div class="holder">
      <p class="holder__name">Delia Pratt</p>
      <p class="holder__title">President</p>
    </div>
    <div class="divider"></div>
    <div class="contacts">
      <div class="contact">
        <svg width="18" height="18" viewBox="0 0 24 24" aria-hidden="true">
          <path fill="#0055a8" d="M6.6 10.8c1.4 2.8 3.8 5.1 6.6 6.6l2.2-2.2c.3-.3.7-.4 1-.2 1.1.4 2.3.6 3.6.6.6 0 1 .4 1 1V20c0 .6-.4 1-1 1C10.6 21 3 13.4 3 4c0-.6.4-1 1-1h3.5c.6 0 1 .4 1 1 0 1.3.2 2.5.6 3.6.1.3 0 .7-.2 1l-2.3 2.2z"/>
          <path fill="none" stroke="#0055a8" stroke-width="1.8" stroke-linecap="round" d="M14 3.5a7 7 0 0 1 6.5 6.5M14 7a3.5 3.5 0 0 1 3 3"/>
        </svg>
        <span>703-555-0142</span>
      </div>
      <div class="contact">
        <svg width="19" height="14" viewBox="0 0 19 14" aria-hidden="true">
          <rect width="19" height="14" rx="1.5" fill="#0055a8"/>
          <path d="M1.5 2l8 5.5 8-5.5" fill="none" stroke="#ffffff" stroke-width="1.6"/>
        </svg>
        <span>prattdq47@mailvessa.com</span>
      </div>
    </div>
  </section>

  <section class="card card--back">
    <div class="wordmark">
      <span class="wordmark__name">TK Verdane</span>
      <span class="wordmark__legal">Consulting LLC</span>
    </div>
  </section>
</div>
</body>
</html>
```